Business Card and Simple Logo Desgin

New Zealand based start up company "Vesta Advisory LTD" requires business cards and simple logo design.

Card Content.

Vesta Advisory LTD

Rebecca Thornbury
CA, BMS (Hons)

r.thornbury@vestaadvisory.co.nz
PH +64 21 574 613

Target Market(s)

Corporate Business in IT, Finance and accounting.

Industry/Entity Type

Business

```html
<!DOCTYPE html>
<html lang="en">
<head>
<meta charset="utf-8">
<title>Vesta Advisory LTD – Business Cards</title>
<link rel="stylesheet" href="https://fonts.googleapis.com/css2?family=Saira+Semi+Condensed:wght@500&family=Arimo:wght@400;700&display=swap">
<style>
  :root {
    --page: #ffffff;
    --blue-light: #1b7cc6;
    --blue-mid: #12589a;
    --blue-dark: #0c3f72;
    --orange: #f4a52b;
    --silver: #d9dde2;
    --ink: #4a4a4a;
    --white: #ffffff;
    --shadow: rgba(0, 0, 0, 0.45);
  }
  * { box-sizing: border-box; margin: 0; padding: 0; }
  html, body {
    width: 1200px; height: 901px; overflow: hidden;
    background: var(--page);
  }
  .canvas { position: relative; width: 1200px; height: 901px; }

  .card {
    position: absolute; left: 260px; width: 636px; height: 364px;
    overflow: hidden;
    box-shadow: 5px 6px 8px var(--shadow);
  }

  /* Front */
  .card-front {
    top: 60px;
    background: radial-gradient(ellipse 60% 75% at 50% 38%, var(--blue-light) 0%, var(--blue-mid) 55%, var(--blue-dark) 100%);
  }
  .front-mark {
    position: absolute; left: 288px; top: 90px; width: 60px; height: 60px;
    background: var(--silver); border-radius: 8px;
  }
  .front-name {
    position: absolute; left: 0; right: 0; top: 206px; text-align: center;
    font-family: "Saira Semi Condensed", sans-serif; font-weight: 500;
    font-size: 38px; line-height: 1; color: var(--silver);
  }
  .front-web {
    position: absolute; left: 0; right: 0; top: 316px; text-align: center;
    font-family: "Saira Semi Condensed", sans-serif; font-weight: 500;
    font-size: 17px; letter-spacing: 0.5px; color: var(--white);
  }
  .front-web .domain { color: var(--orange); }

  /* Back */
  .card-back { top: 496px; background: var(--white); }
  .back-mark {
    position: absolute; left: 60px; top: 78px; width: 58px; height: 58px;
    background: var(--orange); border-radius: 8px;
  }
  .back-name {
    position: absolute; left: 176px; top: 74px;
    font-family: "Saira Semi Condensed", sans-serif; font-weight: 500;
    font-size: 54px; line-height: 1; color: var(--ink);
  }
  .accent-rule {
    position: absolute; left: 0; right: 0; top: 195px; height: 9px;
    background: var(--orange);
  }
  .contact-band {
    position: absolute; left: 0; right: 0; top: 204px; bottom: 0;
    background: linear-gradient(100deg, var(--blue-light) 0%, var(--blue-mid) 55%, var(--blue-dark) 100%);
  }
  .tab-arrow { position: absolute; left: 0; top: 24px; }
  .person {
    position: absolute; left: 53px; top: 31px;
    font-family: "Arimo", sans-serif; color: var(--white);
  }
  .person-name { font-weight: 700; font-size: 20px; color: var(--orange); line-height: 1.1; }
  .person-title { font-size: 16px; margin-top: 3px; }
  .contact-list {
    position: absolute; left: 56px; top: 90px; list-style: none;
    font-family: "Arimo", sans-serif; font-size: 16px; color: var(--white);
  }
  .contact-list li { display: flex; align-items: center; gap: 8px; height: 22px; }
  .contact-list svg { width: 14px; height: 14px; flex: none; }
</style>
</head>
<body>
<div class="canvas">

  <section class="card card-front" aria-label="Card front">
    <div class="front-mark" aria-hidden="true"></div>
    <h1 class="front-name">Vesta Advisory LTD</h1>
    <p class="front-web">www.<span class="domain">vestaadvisory</span>.co.nz</p>
  </section>

  <section class="card card-back" aria-label="Card back">
    <div class="back-mark" aria-hidden="true"></div>
    <h2 class="back-name">Vesta Advisory LTD</h2>
    <div class="accent-rule"></div>
    <div class="contact-band">
      <svg class="tab-arrow" width="24" height="48" viewBox="0 0 24 48" aria-hidden="true">
        <polygon points="0,0 24,24 0,48" fill="var(--orange)"/>
      </svg>
      <div class="person">
        <p class="person-name">Rebecca Thornbury</p>
        <p class="person-title">CA, BMS (Hons)</p>
      </div>
      <ul class="contact-list">
        <li>
          <svg viewBox="0 0 14 14" aria-label="Phone"><rect x="3.5" y="1" width="7" height="12" rx="1.5" fill="none" stroke="var(--orange)" stroke-width="1.6"/><rect x="5" y="3" width="4" height="5" fill="var(--orange)"/></svg>
          <span>+64 21 574 613</span>
        </li>
        <li>
          <svg viewBox="0 0 14 14" aria-label="Email"><rect x="1" y="3" width="12" height="8" fill="var(--orange)"/><polyline points="1,3 7,8 13,3" fill="none" stroke="var(--blue-mid)" stroke-width="1.2"/></svg>
          <span>r.thornbury@vestaadvisory.co.nz</span>
        </li>
      </ul>
    </div>
  </section>

</div>
</body>
</html>
```